Re-style home page - eye-catching and unique design for social commerce website

We need a new concept design for BrinoKet's home page.
We don't want to make huge changes but creating a more professional and eye-catching style.

We need to look very serious like a professional services company and in the same time to look like a social network for e-commerce.

Our logo is very captive and you can use to creating something of harmonious.

This is a re-style and I'm excepted to see unique and fresh design like Glimmora.

Target Market(s)

e-commerce and social

Industry/Entity Type

Social

Number of Pages Required

1 page

Font styles to use
Serif
Sans Serif

Requirements
Must have
• An eye-catching result.
• Search bar with logo and Login How it works and business
• The slogan with login and signup.
• Footer links.
Nice to have
• I would like to open the home page and see only two clear ways:
• -Consumer
• --Search
• --The slogan
• --Login and Signup
• --How it works
• -Business
• --Go to Business area
• Background: City, Shopping.
Should not have
• Scrollbar style!

```html
<!DOCTYPE html>
<html lang="en">
<head>
<meta charset="utf-8">
<title>BrinoKet – Home</title>
<link rel="stylesheet" href="https://fonts.googleapis.com/css2?family=Roboto:wght@400;500;700&display=swap">
<style>
:root{
  --sky-top:#2c5a8e;
  --sky-mid:#3d6590;
  --city-warm:#8a6a52;
  --city-low:#b08a66;
  --panel-grey:#b9b9b9;
  --panel-pink:#c9386e;
  --panel-dark:#3a3a3a;
  --white:#ffffff;
  --ink:#333333;
  --search-blue:#2f80e8;
  --social-blue:#1d36c8;
  --social-blue-dark:#1a2fad;
}
*{box-sizing:border-box;margin:0;padding:0}
html,body{width:1200px;height:1134px;overflow:hidden}
body{font-family:"Roboto",Arial,sans-serif;color:var(--white);position:relative}
.city-backdrop{position:absolute;inset:0;
  background:
    radial-gradient(ellipse 420px 500px at 120px 520px,rgba(40,70,120,.9),transparent 70%),
    radial-gradient(ellipse 500px 300px at 1050px 1000px,rgba(210,150,90,.6),transparent 70%),
    linear-gradient(180deg,var(--sky-top) 0%,var(--sky-mid) 40%,var(--city-warm) 80%,var(--city-low) 100%);}
.search-bar{position:absolute;left:397px;top:53px;width:405px;height:53px;background:var(--white);display:flex;border-radius:2px}
.search-bar input{flex:1;border:0;outline:0;font:400 16px "Roboto",Arial,sans-serif;color:var(--ink);padding-left:20px;background:transparent}
.search-bar input::placeholder{color:#444}
.search-button{width:58px;border:0;border-left:1px solid #e2e2e2;background:var(--white);display:flex;align-items:center;justify-content:center}
.top-links{position:absolute;top:115px;left:395px;width:407px;display:flex;justify-content:space-between;font-size:14px}
.top-links a{color:var(--white);text-decoration:none}
.brand{position:absolute;top:168px;left:0;width:1200px;display:flex;justify-content:center;align-items:center;gap:12px;z-index:2}
.brand-name{font-weight:700;font-size:58px;letter-spacing:-1px;color:var(--white)}
.brand-mark{width:40px;height:40px;background:var(--white)}
.hero-panel{position:absolute;left:190px;top:210px;width:820px;height:819px;overflow:hidden}
.hero-photo{position:absolute;inset:0;
  background:
    linear-gradient(120deg,transparent 35%,rgba(201,56,110,.55) 36%,rgba(201,56,110,.55) 58%,transparent 59%),
    linear-gradient(90deg,var(--panel-grey) 0%,#c4bfbf 55%,#8f6b55 78%,var(--panel-dark) 100%);}
.hero-content{position:absolute;inset:0;text-align:center}
.hero-title{position:absolute;top:55px;width:100%;font-weight:400;font-size:38px}
.feed-title{position:absolute;top:128px;width:100%;font-weight:400;font-size:29px}
.category{position:absolute;width:191px;height:50px;border:2px solid var(--white);display:flex;align-items:center;justify-content:center;text-align:center;font-weight:500;font-size:14px;line-height:19px;color:var(--white);text-transform:uppercase;background:rgba(255,255,255,.04)}
.slogan{position:absolute;top:660px;width:100%;font-weight:400;font-size:24px}
.social-login{position:absolute;left:299px;top:705px;width:222px;height:44px;background:var(--social-blue);display:flex;align-items:center;color:var(--white);font-weight:500;font-size:15px;text-decoration:none}
.social-login .mark{width:44px;height:44px;background:var(--social-blue-dark);display:flex;align-items:center;justify-content:center;margin-right:14px}
.social-login .mark span{width:16px;height:16px;background:var(--white)}
.signup-link{position:absolute;top:764px;width:100%;font-size:19px;color:var(--white);text-decoration:none;display:block}
.footer-links{position:absolute;top:1074px;left:0;width:1200px;display:flex;justify-content:center;font-size:13px}
.footer-links a{color:var(--white);text-decoration:none;padding:0 8px;border-left:1px solid rgba(255,255,255,.8);line-height:13px}
.footer-links a:first-child{border-left:0}
</style>
</head>
<body>
<div class="city-backdrop" role="img" aria-label="Blurred city skyline at dusk with light trails on a highway"></div>

<form class="search-bar">
  <input type="text" placeholder="Search here...">
  <button class="search-button" type="button" aria-label="Search">
    <svg width="26" height="26" viewBox="0 0 26 26"><circle cx="10.5" cy="10.5" r="8" fill="none" stroke="#2f80e8" stroke-width="3"/><line x1="16.5" y1="16.5" x2="24" y2="24" stroke="#2f80e8" stroke-width="3.5" stroke-linecap="round"/></svg>
  </button>
</form>
<nav class="top-links">
  <a href="#">How it work / Business</a>
  <a href="#">Login / Sign up</a>
</nav>

<div class="brand"><span class="brand-name">BrinoKet</span><span class="brand-mark"></span></div>

<main class="hero-panel">
  <div class="hero-photo" role="img" aria-label="Shopper's arm holding a payment card with colourful shopping bags"></div>
  <div class="hero-content">
    <h1 class="hero-title">Shop directly from your Profile</h1>
    <h2 class="feed-title">SETUP YOUR FEED</h2>

    <a class="category" style="left:110px;top:188px">Active Life</a>
    <a class="category" style="left:313px;top:188px">Arts &amp; Entertainment</a>
    <a class="category" style="left:517px;top:188px">Automotive</a>
    <a class="category" style="left:110px;top:252px">Beauti &amp; Spas</a>
    <a class="category" style="left:313px;top:252px">Education</a>
    <a class="category" style="left:517px;top:252px">Event Planning<br>&amp; Services</a>
    <a class="category" style="left:110px;top:316px">Financial Services</a>
    <a class="category" style="left:313px;top:316px">Food</a>
    <a class="category" style="left:517px;top:316px">Health &amp; Medical</a>
    <a class="category" style="left:110px;top:381px">Home Servies</a>
    <a class="category" style="left:313px;top:381px">Hotels</a>
    <a class="category" style="left:517px;top:381px">Local Services</a>
    <a class="category" style="left:110px;top:446px">Mass Media</a>
    <a class="category" style="left:313px;top:446px">Nightlife</a>
    <a class="category" style="left:517px;top:446px">Pets</a>
    <a class="category" style="left:110px;top:512px">Professional<br>Services</a>
    <a class="category" style="left:313px;top:512px">Public Services &amp;<br>Goverment</a>
    <a class="category" style="left:517px;top:512px">Real Estate</a>
    <a class="category" style="left:212px;top:577px">Restaurants</a>
    <a class="category" style="left:415px;top:577px">Shopping</a>

    <p class="slogan">Save Your Time. Live Better</p>
    <a class="social-login" href="#"><span class="mark"><span></span></span>Login with Connectly</a>
    <a class="signup-link" href="#">Sign Up</a>
  </div>
</main>

<footer class="footer-links">
  <a href="#">About us</a><a href="#">Blog</a><a href="#">Business Jobs</a><a href="#">Privacy</a><a href="#">FAQ</a><a href="#">Contacts</a>
</footer>
</body>
</html>
```